accomplished personal trainer, former elite gymnast from Russia, highly professional and experienced

Established Fitness trainer in California requires a new web site to attract personal clients and build her group exercise classes.

Here is an example of another fitness trainer's site that I really liked the technology:
http://www.tedvorlam.com

Below I have inserted my current web site: www.quelbornfitnesslodi.com
You can use this web site for the principal content, such as my background and qualifications.

Target Market(s)

Anyone who wants to improve their fitness levels and wellness in general. Anyone who needs directions and instruction on how to exercise. I can train anyone from elite athlete to a disabled person.

Industry/Entity Type

Fitness

Coding

Coded - Design and coding required

Number of Pages Required

5+ page

Font styles to use
Sans Serif

Requirements
Must have
• Easy to navigate main info about me, location, services, contact, benefits of using my services.
• Would be great to create unique representation of me as a trainer and a person, using new technologies and new ideas. Make it different from the other websites. Having its own character. Not too complicated and heavy with information, but an eye catching, useful and fun to navigate.
Nice to have
• new technology, easy access to information, the idea of enjoyment of life, lightness about achieving any goal, spiritual wisdom, unique design. I am planning to insert educational videos, advise, maybe jokes. Sign in, shopping cart, logo, should be easy for me to make changes in content.
Should not have
• cliché, outdated technology, too complicated,

```html
<!DOCTYPE html>
<html lang="en">
<head>
<meta charset="utf-8">
<title>Quelborn Fitness Lodi</title>
<link href="https://fonts.googleapis.com/css2?family=Lato:ital,wght@0,300;0,400;0,700;0,900;1,400&display=swap" rel="stylesheet">
<style>
:root{
  --green:#4fae6c;
  --green-dark:#3f9a5b;
  --orange:#d98a1f;
  --navy:#2b3a4c;
  --ink:#2f3337;
  --muted:#9aa0a6;
  --line:#e6e8ea;
  --paper:#ffffff;
  --soft:#f3f4f6;
  --footer:#f5f6f8;
}
*{box-sizing:border-box;margin:0;padding:0}
html,body{width:1200px;height:2532px;overflow:hidden}
body{position:relative;background:var(--paper);font-family:'Lato',sans-serif;color:var(--ink)}
.abs{position:absolute}
.topbar{left:0;top:0;width:1200px;height:30px;background:var(--green);color:#fff;font-size:10px}
.topbar .item{top:0;height:30px;display:flex;align-items:center;gap:7px}
.topbar .sep{top:0;width:1px;height:30px;background:rgba(255,255,255,.25)}
.lang-box{width:16px;height:14px;background:#fff;display:inline-block}
.dots{display:flex;gap:9px;align-items:center}
.dots i{display:block;width:10px;height:10px;border-radius:50%;background:rgba(255,255,255,.9)}
.brand{left:0;top:30px;width:1200px;height:60px;display:flex;align-items:center;justify-content:center;font-size:22px;font-weight:400;letter-spacing:.5px;color:#222;border-bottom:1px solid var(--line)}
.nav{left:0;top:90px;width:1200px;height:43px;font-size:10px;font-weight:700;color:#444;letter-spacing:.3px}
.nav a{position:absolute;top:0;height:43px;display:flex;align-items:center;gap:6px;text-decoration:none;color:inherit}
.nav .bar{position:absolute;top:8px;width:1px;height:27px;background:var(--line)}
.nav .search{position:absolute;left:940px;top:10px;width:24px;height:24px;border-radius:50%;background:#e9eaec;display:flex;align-items:center;justify-content:center}
.hero{left:0;top:133px;width:1200px;height:458px;background:linear-gradient(180deg,#8fae6a 0%,#6f9650 35%,#5d8a3e 60%,#7fa25a 100%)}
.hero-title{left:0;top:258px;width:1200px;text-align:center;color:#fff;font-size:46px;font-weight:700}
.hero-sub{left:400px;top:322px;width:400px;text-align:center;color:#fff;font-size:16px;font-weight:700;line-height:26px}
.btn{display:flex;align-items:center;justify-content:center;font-size:9px;font-weight:700;letter-spacing:.3px;text-transform:uppercase}
.btn-orange{background:var(--orange);color:#fff}
.btn-ghost{border:1px solid #fff;color:#fff}
.pager{left:553px;top:537px;display:flex;gap:8px}
.pager span{width:20px;height:20px;border-radius:50%;border:1px solid rgba(255,255,255,.8);color:#fff;font-size:9px;display:flex;align-items:center;justify-content:center}
.pager span.on{background:#fff;color:#333}
.slide-arrow{top:343px;width:37px;height:37px;display:flex;align-items:center;justify-content:center}
.quote{left:0;top:591px;width:1200px;height:98px;background:var(--soft);text-align:center}
.quote p{position:absolute;left:0;top:25px;width:1200px;font-size:15px;font-style:italic;color:#666;line-height:21px}
.quote cite{position:absolute;left:0;top:662px;width:1200px}
.quote .who{position:absolute;left:0;top:72px;width:1200px;font-size:8px;font-style:italic;color:#999}
.quote-next{left:910px;top:623px;width:30px;height:30px;border-radius:50%;border:1px solid #ccd0d4}
.card{top:793px;width:230px;height:186px;border:1px solid var(--line);background:#fff;text-align:center}
.card .icon{position:absolute;left:84px;top:-32px;width:62px;height:62px;border-radius:50%;background:var(--green);display:flex;align-items:center;justify-content:center}
.card.active .icon{background:var(--navy);box-shadow:0 0 0 3px var(--orange)}
.card h3{position:absolute;left:0;top:52px;width:100%;font-size:11px;font-weight:700}
.card p{position:absolute;left:25px;top:72px;width:180px;font-size:8px;color:var(--muted);line-height:13px}
.card .btn{position:absolute;left:71px;top:130px;width:88px;height:25px;border:1px solid #ddd;color:#999;font-weight:400;text-transform:none}
.card.active .btn{background:var(--orange);border-color:var(--orange);color:#fff}
.section-title{left:0;width:1200px;text-align:center;font-size:22px;font-weight:300;color:#444}
.section-sub{left:0;width:1200px;text-align:center;font-size:8px;font-style:italic;color:#aaa}
.video{top:1119px;height:196px;border:1px solid #ddd}
.play{position:absolute;left:50%;top:50%;width:30px;height:30px;margin:-15px 0 0 -15px;border-radius:50%;background:#fff;display:flex;align-items:center;justify-content:center}
.round-arrow{top:1194px;width:32px;height:32px;border-radius:50%;display:flex;align-items:center;justify-content:center}
.stats{left:0;top:1384px;width:1200px;height:186px;background:var(--green);color:#fff}
.stat{top:58px;width:180px;margin-left:-90px;text-align:center}
.stat b{display:block;font-size:46px;font-weight:300;line-height:46px}
.stat span{display:block;font-size:10px;margin-top:6px}
.feature{left:235px;top:1703px;width:356px;height:262px}
.feature .dark{position:absolute;left:0;top:0;width:185px;height:262px;background:#262626;color:#fff;padding:20px 18px}
.feature h4{font-size:15px;font-weight:700;margin-bottom:12px}
.feature .dark p{font-size:8px;line-height:13px;color:#cfcfcf}
.feature .date{font-size:9px;font-weight:700;margin-top:12px}
.feature .ctrl{display:flex;gap:4px;margin-top:12px}
.feature .ctrl i{width:17px;height:17px;border:1px solid #777;display:block}
.feature .ctrl i.on{background:var(--orange);border-color:var(--orange)}
.feature .photo{position:absolute;left:185px;top:0;width:171px;height:262px;background:linear-gradient(160deg,#3f5a2c,#5d7a3c 50%,#2e6a9a 75%,#3c4f2a)}
.post{left:609px;width:355px;height:93px;border-bottom:1px solid var(--line)}
.post .thumb{position:absolute;left:0;top:0;width:62px;height:74px}
.post .thumb .img{position:absolute;left:0;top:0;width:62px;height:58px;background:linear-gradient(180deg,#7aa35a,#4f7a3a)}
.post .thumb .day{position:absolute;left:0;top:58px;width:62px;height:16px;background:var(--navy);color:#fff;font-size:9px;display:flex;align-items:center;justify-content:center}
.post .thumb.big{background:var(--green);color:#fff;font-size:28px;display:flex;align-items:flex-start;justify-content:center;padding-top:12px}
.post h5{position:absolute;left:75px;top:0;width:280px;font-size:11px;font-weight:700;color:#333}
.post h5.hl{color:var(--green)}
.post p{position:absolute;left:75px;top:18px;width:275px;font-size:8px;line-height:12px;color:var(--muted)}
.post .meta{position:absolute;left:75px;top:65px;font-size:9px;color:var(--green);word-spacing:2px}
.post .meta em{font-style:normal;color:#bbb;margin:0 8px}
.news{left:235px;top:2037px;width:729px;height:92px;border:1px solid var(--line);border-left:5px solid var(--orange);background:#fff}
.news h6{position:absolute;left:19px;top:20px;font-size:14px;font-weight:400;color:#333}
.news p{position:absolute;left:19px;top:44px;width:300px;font-size:8px;line-height:12px;color:var(--muted)}
.news .field{position:absolute;left:360px;top:30px;width:220px;height:30px;background:#eceef0;font-size:8px;color:#888;display:flex;align-items:center;padding-left:12px}
.news .btn{position:absolute;left:584px;top:30px;width:110px;height:30px;font-size:11px;text-transform:none;font-weight:400}
.footer-rule{left:0;top:2171px;width:1200px;height:7px;background:var(--green)}
.footer{left:0;top:2178px;width:1200px;height:295px;background:var(--footer)}
.fcol{top:54px;width:165px}
.fcol h6{font-size:10px;font-weight:900;letter-spacing:2px;color:#333;padding-bottom:8px;position:relative}
.fcol h6::after{content:"";position:absolute;left:0;bottom:0;width:42px;height:2px;background:var(--navy)}
.fcol ul{list-style:none;margin-top:24px}
.fcol li{height:51px;border-bottom:1px solid #e7e9ec;padding-top:4px}
.fcol li:last-child{border-bottom:none}
.fcol li b{display:block;font-size:10px;font-weight:700;color:#333}
.fcol li span{display:block;font-size:8px;color:var(--muted);margin-top:4px}
.fabout h5{font-size:15px;font-weight:400;color:#333;margin-top:30px}
.fabout p{font-size:8px;line-height:14px;color:var(--muted);margin-top:22px}
.fabout a{display:block;font-size:8px;font-weight:900;color:#333;margin-top:4px;text-decoration:none}
.bottom{left:0;top:2473px;width:1200px;height:59px;background:#fff}
.bottom .copy{position:absolute;left:235px;top:24px;font-size:8px;color:#999}
.bottom .dots{position:absolute;left:817px;top:24px}
.bottom .dots i{background:#b7bcc2;width:9px;height:9px}
</style>
</head>
<body>

<header>
  <div class="abs topbar">
    <div class="abs item" style="left:245px">
      <svg width="10" height="10" viewBox="0 0 10 10"><circle cx="5" cy="5" r="4" fill="none" stroke="#fff"/><line x1="1" y1="5" x2="9" y2="5" stroke="#fff"/></svg>
      Languages: <b>English</b> <span class="lang-box"></span>
    </div>
    <div class="abs sep" style="left:370px"></div>
    <div class="abs item" style="left:385px">
      <svg width="9" height="9" viewBox="0 0 10 10"><path d="M2 1l2 2-1 1.5c.8 1.5 1.8 2.5 3.3 3.3L7.8 6.8l2 2L8.6 10C4.5 9.5.5 5.5 0 1.4z" fill="#fff"/></svg>
      +1 (209) 555-0147
    </div>
    <div class="abs sep" style="left:490px"></div>
    <div class="abs item" style="left:503px">
      <svg width="11" height="8" viewBox="0 0 11 8"><rect x=".5" y=".5" width="10" height="7" fill="none" stroke="#fff"/><path d="M.5.5l5 4 5-4" fill="none" stroke="#fff"/></svg>
      hello@quelbornfit.net
    </div>
    <div class="abs sep" style="left:635px"></div>
    <div class="abs item dots" style="left:787px"><i></i><i></i><i></i><i></i><i></i><i></i><i></i><i></i><i></i></div>
  </div>

  <div class="abs brand">QUELBORN FITNESS LODI</div>

  <nav class="abs nav">
    <a href="#" style="left:234px">
      <svg width="9" height="9" viewBox="0 0 10 10"><path d="M5 0l5 5H8.5v5h-2.5V7H4v3H1.5V5H0z" fill="var(--green)"/></svg>HOME</a>
    <span class="bar" style="left:297px"></span>
    <a href="#" style="left:320px">GROUP CLASSES</a>
    <span class="bar" style="left:419px"></span>
    <a href="#" style="left:435px">PERSONAL TRAINING</a>
    <span class="bar" style="left:545px"></span>
    <a href="#" style="left:560px">ABOUT QUELBORN</a>
    <span class="bar" style="left:662px"></span>
    <a href="#" style="left:680px">CONTACT</a>
    <span class="bar" style="left:743px"></span>
    <a href="#" style="left:766px">BLOG</a>
    <span class="search"><svg width="10" height="10" viewBox="0 0 10 10"><circle cx="4" cy="4" r="3" fill="none" stroke="#666" stroke-width="1.2"/><line x1="6.2" y1="6.2" x2="9" y2="9" stroke="#666" stroke-width="1.2"/></svg></span>
  </nav>
</header>

<section>
  <div class="abs hero" role="img" aria-label="Group of people doing squats together outdoors on a sunny park lawn"></div>
  <h1 class="abs hero-title">Fitness Outdoors</h1>
  <p class="abs hero-sub">Nam ornare diam eu porta rutrum. In faucibus mi diam, et efficitur mauris semper a.</p>
  <a class="abs btn btn-orange" style="left:493px;top:400px;width:106px;height:32px">Read More</a>
  <a class="abs btn btn-ghost" style="left:611px;top:400px;width:106px;height:32px">Online Booking</a>
  <div class="abs pager"><span>1</span><span class="on">2</span><span>3</span><span>4</span></div>
  <div class="abs slide-arrow" style="left:0;background:var(--orange)"><svg width="8" height="10" viewBox="0 0 8 10"><path d="M6 1L2 5l4 4" fill="none" stroke="#fff" stroke-width="1.6"/></svg></div>
  <div class="abs slide-arrow" style="left:1163px;background:#2a2f35"><svg width="8" height="10" viewBox="0 0 8 10"><path d="M2 1l4 4-4 4" fill="none" stroke="#fff" stroke-width="1.6"/></svg></div>
</section>

<section class="abs quote">
  <p>“The best thing about working out with Mirela is the variety she offers in each workout.<br>I always leave feeling that I tried something new.”</p>
  <span class="who">— Owen Falk</span>
</section>
<div class="abs quote-next"></div>

<section>
  <article class="abs card" style="left:235px">
    <div class="icon"><svg width="24" height="22" viewBox="0 0 24 22"><circle cx="12" cy="6" r="4" fill="#fff"/><circle cx="5" cy="9" r="3" fill="#fff"/><circle cx="19" cy="9" r="3" fill="#fff"/><path d="M5 20c0-5 3-8 7-8s7 3 7 8z" fill="#fff"/></svg></div>
    <h3>Group Classes/ Boot Camps</h3>
    <p>Praesent turpis mauris, aliquet id dolor Gravida adipiscing lectus ut rutrum Aenean at posuere risus.</p>
    <a class="btn">Read More</a>
  </article>
  <article class="abs card active" style="left:484px">
    <div class="icon"><svg width="26" height="22" viewBox="0 0 26 22"><circle cx="8" cy="5" r="3" fill="#fff"/><rect x="3" y="10" width="20" height="3" fill="#fff"/><rect x="4" y="13" width="2" height="7" fill="#fff"/><rect x="20" y="13" width="2" height="7" fill="#fff"/><rect x="14" y="3" width="2" height="8" fill="#fff"/></svg></div>
    <h3>Personal Training</h3>
    <p>Praesent turpis mauris, aliquet id dolor Gravida adipiscing lectus ut rutrum Aenean at posuere risus.</p>
    <a class="btn">Read More</a>
  </article>
  <article class="abs card" style="left:734px">
    <div class="icon"><svg width="26" height="26" viewBox="0 0 26 26"><circle cx="13" cy="13" r="11" fill="none" stroke="#fff" stroke-width="2"/><circle cx="13" cy="8" r="1.6" fill="#fff"/><rect x="11.6" y="11" width="2.8" height="9" fill="#fff"/></svg></div>
    <h3>About Quelborn Fitness</h3>
    <p>Praesent turpis mauris, aliquet id dolor Gravida adipiscing lectus ut rutrum Aenean at posuere risus.</p>
    <a class="btn">Read More</a>
  </article>
</section>

<section>
  <h2 class="abs section-title" style="top:1037px">Educational Videos</h2>
  <p class="abs section-sub" style="top:1072px">Lorem ipsum dolor sit amet, consectetur</p>
  <div class="abs video" style="left:235px;width:354px;background:linear-gradient(170deg,#6f8f4a,#8aa85c 55%,#5f8a3a)" role="img" aria-label="Video still of a woman stretching on a lawn in a park">
    <span class="play"><svg width="10" height="12" viewBox="0 0 10 12"><path d="M1 0l9 6-9 6z" fill="#333"/></svg></span>
  </div>
  <div class="abs video" style="left:611px;width:353px;background:linear-gradient(170deg,#5f7d3e,#7e9c55 55%,#4f7a35)" role="img" aria-label="Video still of a group stretching together under trees">
    <span class="play"><svg width="10" height="12" viewBox="0 0 10 12"><path d="M1 0l9 6-9 6z" fill="#333"/></svg></span>
  </div>
  <div class="abs round-arrow" style="left:151px;background:var(--navy)"><svg width="8" height="10" viewBox="0 0 8 10"><path d="M6 1L2 5l4 4" fill="none" stroke="#fff" stroke-width="1.6"/></svg></div>
  <div class="abs round-arrow" style="left:1015px;background:var(--orange)"><svg width="8" height="10" viewBox="0 0 8 10"><path d="M2 1l4 4-4 4" fill="none" stroke="#fff" stroke-width="1.6"/></svg></div>
</section>

<section class="abs stats">
  <div class="abs stat" style="left:317px"><b>2.438</b><span>Customers</span></div>
  <div class="abs stat" style="left:500px"><b>9.845</b><span>Works</span></div>
  <div class="abs stat" style="left:694px"><b>9.845</b><span>Classes</span></div>
  <div class="abs stat" style="left:876px"><b>1.276</b><span>Support Posts</span></div>
</section>

<section>
  <h2 class="abs section-title" style="top:1617px">Tips to Members</h2>
  <p class="abs section-sub" style="top:1650px">Donec suscipit, diam condimentum viverra ornare, turpis ipsum molestie quam</p>

  <article class="abs feature">
    <div class="dark">
      <h4>Lacinia at sollicitudin</h4>
      <p>Vivamus viverra, ligula non tincidunt pulvinar, augue est sagittis leo, id feugiat enim lorem quis nisl. Quisque ac arcu egestas, convallis risus vitae, gravida enim.</p>
      <div class="date">27 Feb, 2016</div>
      <div class="ctrl"><i class="on"></i><i></i></div>
    </div>
    <div class="photo" role="img" aria-label="Photo of a person in workout wear stretching outdoors among trees"></div>
  </article>

  <article class="abs post" style="top:1703px">
    <div class="thumb big">29<span class="day">Nov</span></div>
    <h5 class="hl">Pellentesque lorem massa, lacinia at sollicitudin</h5>
    <p>Lorem ipsum dolor sit amet, consectetur adipiscing elit. Vivamus a aliquet orci. Ut interdum mauris, non aliquet felis interdum id</p>
    <div class="meta">27 comments<em>/</em>Blog Design<em>/</em>Read more</div>
  </article>
  <article class="abs post" style="top:1796px">
    <div class="thumb"><div class="img" role="img" aria-label="Small photo of people exercising outdoors"></div><span class="day">29, Nov</span></div>
    <h5>Massa, lacinia at sollicitudin</h5>
    <p>Lorem ipsum dolor sit amet, consectetur adipiscing elit. Vivamus a aliquet orci. Ut interdum mauris, non aliquet felis interdum id</p>
    <div class="meta">27 comments<em>/</em>Blog Design<em>/</em>Read more</div>
  </article>
  <article class="abs post" style="top:1889px;border-bottom:none">
    <div class="thumb"><div class="img" role="img" aria-label="Small photo of women training in a park"></div><span class="day">29, Nov</span></div>
    <h5>Lorem massa, lacinia at sollicitudin</h5>
    <p>Lorem ipsum dolor sit amet, consectetur adipiscing elit. Vivamus a aliquet orci. Ut interdum mauris, non aliquet felis interdum id</p>
    <div class="meta">27 comments<em>/</em>Blog Design<em>/</em>Read more</div>
  </article>
</section>

<section class="abs news">
  <h6>Subscribe for Newsletter</h6>
  <p>Quisque lacinia tortor in mauris egestas, nec adipiscing nisl auctor. Suspendisse potenti. Nam in consequat turpis.</p>
  <div class="field">Enter email id</div>
  <a class="btn btn-orange">Subscribe</a>
</section>

<div class="abs footer-rule"></div>
<footer class="abs footer">
  <div class="abs fcol" style="left:235px">
    <h6>RECENT POST</h6>
    <ul>
      <li><b>Amazing Standard Post</b><span>26 May, 2017</span></li>
      <li><b>Slideshow Images</b><span>26 May, 2017</span></li>
      <li><b>Video Post</b><span>26 May, 2017</span></li>
    </ul>
  </div>
  <div class="abs fcol" style="left:422px">
    <h6>RECENT COMMENTS</h6>
    <ul>
      <li><b>Lena Ortiz</b><span>Popular sit lorem ipsum dolor sit amet</span></li>
      <li><b>Paul Reyes</b><span>Lorem ipsum dolor sit amet</span></li>
      <li><b>Mara Quinn</b><span>Contrary lorem ipsum dolor sit amet</span></li>
    </ul>
  </div>
  <div class="abs fcol" style="left:609px">
    <h6>ARCHIVES</h6>
    <ul>
      <li><b>March 2017</b><span>1509 Posted</span></li>
      <li><b>June 2017</b><span>1509 Posted</span></li>
      <li><b>July 2017</b><span>1509 Posted</span></li>
    </ul>
  </div>
  <div class="abs fcol fabout" style="left:797px">
    <h6>ABOUT US</h6>
    <h5>QUELBORN FITNESS LODI</h5>
    <p>We are constantly working to raise the bar on our services. If you have any questions or concerns about your experience, please let us know.</p>
    <a href="#">LEARN MORE</a>
  </div>
</footer>

<div class="abs bottom">
  <span class="copy">© 2016 Quelborn Fitness. All Rights Reserved.</span>
  <div class="dots"><i></i><i></i><i></i><i></i><i></i><i></i><i></i><i></i></div>
</div>

</body>
</html>
```